Real Estate Business Card

Our Company, Brovan Real Estate needs a business card design. It will need a spot for our Name, Office Number, Cell number, email, website address. Brovanrealestate.example and Address. Please utilize our logo for the aesthetic feel of the card. We would like something that is noticeable but looks professional.

Please include our company tagline. "Where Every New Move Feels Simple and Right"

Industry/Entity Type

Business

Requirements
Should not have
• Black colored Font is OK. But other than that no black

```html
<!DOCTYPE html>
<html lang="en">
<head>
<meta charset="utf-8">
<title>Brovan Real Estate – Business Card</title>
<link rel="stylesheet" href="https://fonts.googleapis.com/css2?family=Open+Sans:wght@400;600;700;800&display=swap">
<style>
  :root {
    --orange: #e8711f;
    --blue: #2b62b0;
    --ink: #1a1a1a;
    --paper: #ffffff;
    --backdrop: #e6e7ea;
  }
  * { box-sizing: border-box; margin: 0; padding: 0; }
  html, body { width: 1200px; height: 723px; overflow: hidden; }
  body {
    background: var(--backdrop);
    font-family: "Open Sans", Arial, sans-serif;
    display: flex;
    align-items: center;
    justify-content: center;
    gap: 50px;
  }
  .card {
    position: relative;
    width: 520px;
    height: 297px;
    background: var(--paper);
    box-shadow: 0 4px 14px rgba(0,0,0,0.15);
    overflow: hidden;
  }

  /* Front */
  .front-brand {
    position: absolute;
    left: 0; right: 0; top: 88px;
    display: flex;
    flex-direction: column;
    align-items: center;
  }
  .brand-row { display: flex; align-items: center; gap: 12px; }
  .brand-mark {
    width: 34px; height: 34px;
    background: var(--orange);
    border-radius: 4px;
  }
  .brand-name {
    font-size: 38px;
    font-weight: 600;
    color: var(--blue);
    letter-spacing: -0.5px;
  }
  .tagline {
    margin-top: 4px;
    padding-left: 46px;
    font-size: 13px;
    font-weight: 800;
    color: var(--ink);
  }
  .front-bands { position: absolute; left: 0; right: 0; bottom: 0; }
  .front-bands .thin { height: 3px; background: var(--blue); margin-bottom: 5px; }
  .front-bands .wide { height: 36px; background: var(--orange); }

  /* Back */
  .back-brand {
    position: absolute;
    left: 26px; top: 24px;
    font-size: 18px;
    font-weight: 600;
    color: var(--orange);
  }
  .person {
    position: absolute;
    right: 34px; top: 56px;
    text-align: right;
  }
  .person-name { font-size: 19px; font-weight: 800; color: var(--blue); }
  .person-title { font-size: 12px; color: var(--blue); margin-top: -2px; }
  .contacts {
    position: absolute;
    right: 30px; top: 122px;
    list-style: none;
  }
  .contacts li {
    display: flex;
    justify-content: flex-end;
    align-items: center;
    gap: 6px;
    font-size: 12.5px;
    font-weight: 700;
    line-height: 20px;
  }
  .contacts .blue { color: var(--blue); }
  .contacts .orange { color: var(--orange); }
  .contacts svg { width: 13px; height: 13px; flex: none; }
  .back-bands { position: absolute; left: 0; right: 0; bottom: 0; }
  .back-bands .thin { height: 3px; background: var(--orange); margin-bottom: 5px; }
  .back-bands .wide { height: 40px; background: var(--blue); }
</style>
</head>
<body>

<section class="card card-front">
  <div class="front-brand">
    <div class="brand-row">
      <span class="brand-mark"></span>
      <span class="brand-name">Brovan Real Estate</span>
    </div>
    <p class="tagline">Where Every New Move Feels Simple and Right</p>
  </div>
  <div class="front-bands"><div class="thin"></div><div class="wide"></div></div>
</section>

<section class="card card-back">
  <div class="back-brand">Brovan Real Estate</div>
  <div class="person">
    <p class="person-name">YOUR NAME</p>
    <p class="person-title">Title</p>
  </div>
  <ul class="contacts">
    <li class="blue">Name of place, City, Country, NY 1234
      <svg viewBox="0 0 16 16"><path fill="var(--blue)" d="M8 1a5 5 0 0 0-5 5c0 4 5 9 5 9s5-5 5-9a5 5 0 0 0-5-5zm0 7a2 2 0 1 1 0-4 2 2 0 0 1 0 4z"/></svg></li>
    <li class="orange">123 56 789
      <svg viewBox="0 0 16 16"><path fill="var(--blue)" d="M4 1l3 3-2 2c1 2 3 4 5 5l2-2 3 3-2 3C7 15 1 9 1 3z"/></svg></li>
    <li class="orange">123 456 0987
      <svg viewBox="0 0 16 16"><rect x="4" y="1" width="8" height="14" rx="1.5" fill="none" stroke="var(--blue)" stroke-width="1.6"/><circle cx="8" cy="12.5" r="0.9" fill="var(--blue)"/></svg></li>
    <li class="orange">yourname@brovanestate.example
      <svg viewBox="0 0 16 16"><rect x="1" y="3" width="14" height="10" fill="var(--blue)"/><path d="M1 3l7 6 7-6" fill="none" stroke="#fff" stroke-width="1.3"/></svg></li>
    <li class="orange">Brovanrealestate.example
      <svg viewBox="0 0 16 16"><circle cx="8" cy="8" r="6.5" fill="none" stroke="var(--blue)" stroke-width="1.4"/><path d="M1.5 8h13M8 1.5c-3 3.5-3 9.5 0 13M8 1.5c3 3.5 3 9.5 0 13" fill="none" stroke="var(--blue)" stroke-width="1.1"/></svg></li>
  </ul>
  <div class="back-bands"><div class="thin"></div><div class="wide"></div></div>
</section>

</body>
</html>
```